4D Cradle Glimpse Luxury Ultrasound Billboard

Design a HIGH-END, MODERN billboard for my private prenatal ultrasound studio, 4D Cradle Glimpse, located in Pace, Florida.
This billboard will be viewed by drivers traveling at highway speeds, so it must be extremely clean, simple, and readable within 6 seconds.
About My Business
4D Cradle Glimpse is a private prenatal ultrasound studio specializing in:
Highest technology 4D/HD Ultrasounds
Early Gender Determination
Pregnancy Confirmation
I have been serving families for nearly 10 years and is known for creating a memorable experience, not just an ultrasound appointment.
Design Style
I DO NOT want:
Flowers
Leaves
Swirls
Glitter
Hearts everywhere
Busy backgrounds
Generic maternity stock graphics
I DO want:
Modern
Luxury
Upscale
Clean
Professional
Eye-catching
Premium medical spa feel
Colors
Use colors from my logo:
LOGO Green ( or a deep green)
Black
White
Soft Gold accents
Images:
Incorporate my professional headshot in a clean, modern way, logo, and the ultrasound images
Text
Keep wording minimal.
Primary Headline ( OPEN TO IDEAS) :
EXAMPLES ( WOULD RATHER SOMETHING MORE CATCHY)
" ADVANCED IMAGING. UNFORGETTABLE MOMENTS"
"MEET YOUR BABY BEFORE BIRTH"
Under headline:
4D Ultrasound • Early Gender • Pregnancy Confirmation
Business Name:
4D Cradle Glimpse
Private Prenatal Ultrasound Studio
Phone Number:
850-471-5923
Important
This billboard must be readable in 5–6 seconds from a moving vehicle.
Less text is better.
The phone number and business name must be visible from a distance.
The design should feel like a premium brand that immediately tells expecting parents:
“This is where I go to see my baby.”
Files Provided
Official logo
Headshot
Ultrasound images
Don’t make this look like a medical office billboard.
Make it look like a luxury baby experience billboard. That’s what separates 4D Cradle Glimpse from hospitals, OB offices, and all the new studios popping up around you. The emotional connection is what gets moms to book. ❤️
Billboard Size - 10.6” x 36”

```html
<!DOCTYPE html>
<html lang="en">
<head>
<meta charset="utf-8">
<title>4D Cradle Glimpse Billboard</title>
<link rel="stylesheet" href="https://fonts.googleapis.com/css2?family=Krona+One&family=Montserrat:wght@600&display=swap">
<style>
  :root {
    --stage: #cccccc;
    --green: #44695a;
    --gold: #c0950a;
    --white: #ffffff;
    --ink: #1a1a1a;
  }
  * { margin: 0; padding: 0; box-sizing: border-box; }
  html, body { width: 1200px; height: 463px; overflow: hidden; background: var(--stage); }
  .billboard {
    position: absolute; left: 64px; top: 74px;
    width: 1071px; height: 315px;
    background: var(--white); overflow: hidden;
  }
  .headshot {
    position: absolute; left: 4px; top: 3px; width: 190px; height: 252px;
    background: linear-gradient(90deg, #6b5a3f 0%, #c9b089 35%, #e9ddc8 60%, #f7f4ef 85%, #ffffff 100%);
  }
  .ultrasound {
    position: absolute; left: 0; top: 0; width: 1071px; height: 315px;
  }
  .swoosh { position: absolute; left: 0; top: 0; width: 1071px; height: 315px; }
  .headline {
    position: absolute; left: 204px; width: 660px; text-align: center;
    font-family: "Krona One", sans-serif; color: var(--green);
    font-size: 49px; line-height: 56px; letter-spacing: 1px;
    top: 18px;
  }
  .services {
    position: absolute; left: 204px; width: 660px; text-align: center;
    font-family: "Krona One", sans-serif; color: var(--gold);
    font-size: 24px; line-height: 38px; top: 131px;
  }
  .contact {
    position: absolute; left: 193px; top: 270px; display: flex; align-items: center; gap: 10px;
  }
  .contact-icon { width: 36px; height: 36px; }
  .contact-number {
    font-family: "Krona One", sans-serif; color: var(--white);
    font-size: 42px; line-height: 44px; letter-spacing: 1px;
  }
  .brand-card {
    position: absolute; left: 860px; top: 207px; width: 204px; height: 100px;
    background: var(--white); border-radius: 10px;
    display: flex; flex-direction: column; align-items: center; justify-content: center; gap: 10px;
  }
  .brand-name {
    font-family: "Krona One", sans-serif; color: var(--green);
    font-size: 14px; text-align: center; line-height: 20px;
  }
  .brand-tagline {
    font-family: "Montserrat", sans-serif; font-weight: 600; color: var(--green);
    font-size: 8.5px; letter-spacing: 0.4px;
  }
</style>
</head>
<body>
  <div class="billboard">
    <div class="headshot" role="img" aria-label="Professional headshot of the studio owner"></div>

    <svg class="ultrasound" viewBox="0 0 1071 315" role="img" aria-label="4D ultrasound image of twin babies">
      <defs>
        <radialGradient id="scanTone" cx="0.55" cy="0.45" r="0.7">
          <stop offset="0" stop-color="#b5695a"/>
          <stop offset="0.6" stop-color="#7a3a2e"/>
          <stop offset="1" stop-color="#2a120e"/>
        </radialGradient>
      </defs>
      <circle cx="1020" cy="98" r="118" fill="url(#scanTone)" stroke="var(--gold)" stroke-width="2"/>
    </svg>

    <svg class="swoosh" viewBox="0 0 1071 315" aria-hidden="true">
      <path d="M0 252 Q 500 235 1071 171 L1071 315 L0 315 Z" fill="var(--gold)"/>
      <path d="M0 268 Q 500 250 1071 185 L1071 315 L0 315 Z" fill="var(--green)"/>
    </svg>

    <h1 class="headline">MEET YOUR BABY<br>BEFORE BIRTH</h1>
    <p class="services">4D Ultrasound • Early Gender<br>• Pregnancy Confirmation</p>

    <div class="contact">
      <svg class="contact-icon" viewBox="0 0 36 36" aria-hidden="true">
        <circle cx="18" cy="18" r="17" fill="var(--gold)" stroke="var(--ink)" stroke-width="1"/>
        <path d="M12 9c1-1 2-1 3 0l2 3c.6 1 .4 2-.4 2.6l-1.2 1c.8 2 2.4 3.8 4.4 4.8l1-1.2c.6-.8 1.6-1 2.6-.4l3 2c1 .6 1 1.8 0 2.8l-1.4 1.4c-1.4 1.4-4 1-7-1.2-3-2.2-5.6-5.2-6.8-8.2-1-2.6-.6-4.6.8-5.8z" fill="var(--ink)"/>
      </svg>
      <span class="contact-number">850-471-5923</span>
    </div>

    <div class="brand-card">
      <p class="brand-name">4D Cradle Glimpse</p>
      <p class="brand-tagline">PRENATAL ULTRASOUND STUDIO</p>
    </div>
  </div>
</body>
</html>
```